A ebook cover to reinvent the imagery of vegetable companion gardening

We needs a ebook design with illustrates minimal as well as clear and concise relevance to vegetable companion gardening . we will add a mock up design and other existing designs to help you gauge and create the sort of illustration fit for our aims.
Book Title: Orchard and Greens 202 – Garden Partner Sowing
Subtitle: Partner Handbook On Raising Crops Through Basic, Natural & Lasting Plot Methods
(Perfect For Beginners)
Author: Amber Hollow
Size: 5.5 x 8.5

```html
<!DOCTYPE html>
<html lang="en">
<head>
<meta charset="utf-8">
<title>Orchard and Greens 202 – Garden Partner Sowing</title>
<link rel="stylesheet" href="https://fonts.googleapis.com/css2?family=Bebas+Neue&family=Poppins:wght@400;600;700&display=swap">
<style>
  :root {
    --page-bg: #f0f0f0;
    --board-white: #f7f8fa;
    --plank-line: rgba(170, 176, 186, 0.28);
    --title-orange: #df5812;
    --title-green: #3a5a20;
    --pill-black: #141414;
    --text-dark: #1c1c1c;
    --band-orange: #df5812;
    --white: #ffffff;
    --produce-red: #c94436;
    --produce-green: #6f8f3a;
    --produce-purple: #8a4a86;
    --produce-yellow: #e8b52a;
  }
  * { box-sizing: border-box; margin: 0; padding: 0; }
  html, body {
    width: 686px;
    height: 1200px;
    overflow: hidden;
    background: var(--page-bg);
  }
  .cover {
    position: absolute;
    left: 23px;
    top: 105px;
    width: 640px;
    height: 990px;
    background:
      repeating-linear-gradient(90deg,
        transparent 0, transparent 94px,
        var(--plank-line) 94px, var(--plank-line) 96px),
      var(--board-white);
    box-shadow: 0 6px 18px rgba(0,0,0,0.18);
    overflow: hidden;
  }
  .title {
    position: absolute;
    left: 0;
    top: 50px;
    width: 100%;
    text-align: center;
    font-family: "Bebas Neue", "Oswald", sans-serif;
    font-weight: 400;
    font-size: 132px;
    line-height: 118px;
  }
  .title-line-top { display: block; color: var(--title-orange); }
  .title-line-bottom { display: block; color: var(--title-green); }
  .series-pill {
    position: absolute;
    left: 56px;
    top: 298px;
    width: 528px;
    height: 42px;
    border-radius: 21px;
    background: var(--pill-black);
    color: var(--white);
    font-family: "Poppins", sans-serif;
    font-weight: 700;
    font-size: 24px;
    line-height: 42px;
    text-align: center;
  }
  .subtitle {
    position: absolute;
    left: 70px;
    top: 350px;
    width: 500px;
    text-align: center;
    font-family: "Poppins", sans-serif;
    font-weight: 600;
    font-size: 18px;
    line-height: 23px;
    color: var(--text-dark);
  }
  .audience-note {
    display: block;
  }
  .produce-art {
    position: absolute;
    left: 70px;
    top: 452px;
    width: 490px;
    height: 410px;
    background:
      radial-gradient(ellipse closest-side at 50% 30%, var(--produce-red) 0%, rgba(201,68,54,0) 100%),
      radial-gradient(ellipse closest-side at 62% 50%, var(--produce-purple) 0%, rgba(138,74,134,0) 100%),
      radial-gradient(ellipse closest-side at 40% 52%, var(--produce-yellow) 0%, rgba(232,181,42,0) 100%),
      radial-gradient(ellipse closest-side at 50% 62%, var(--produce-green) 0%, rgba(111,143,58,0) 100%);
    opacity: 0.55;
  }
  .author-band {
    position: absolute;
    left: 0;
    bottom: 0;
    width: 100%;
    height: 108px;
    background: var(--band-orange);
    color: var(--white);
    font-family: "Poppins", sans-serif;
    font-weight: 400;
    font-size: 36px;
    letter-spacing: 3px;
    line-height: 108px;
    text-align: center;
  }
</style>
</head>
<body>
  <main class="cover">
    <h1 class="title">
      <span class="title-line-top">Orchard and</span>
      <span class="title-line-bottom">Greens 202</span>
    </h1>
    <p class="series-pill">GARDEN PARTNER SOWING</p>
    <p class="subtitle">Partner Handbook On Raising Crops Through Basic, Natural &amp; Lasting Plot Methods <span class="audience-note">(Perfect For Beginners)</span></p>
    <div class="produce-art" role="img" aria-label="Wicker basket filled with peppers, red cabbage, tomatoes, onions, lettuce and lemons"></div>
    <footer class="author-band">AMBER HOLLOW</footer>
  </main>
</body>
</html>
```